Package Design - Disposable Face Towel

Hi,

We are needing assistance with graphic design on our box/carton/package.

The attached image that is white is our biggest competitor.

Our brand is "VELMORA BATH CO." Please see the logo we uploaded.

Oder we have in mind for front of box:

Logo
LARGE TOWELS
50 Count
Ultra Soft| 100% USDA Bio-Based|100% Eucalyptus Viscose | Vegan
VELMORABATHCO.COM

We like medium to dark blue on most of the box, with white and minimal hot pink or salmon. Something that is sharp, modern, and stands out from our competitors.

Box dimensions are: 6.25 x 5.25 x 4.75 inches

This will be 1 of many design projects.

Target Market(s)

Female Beauty Products

Font styles to use
Serif
Sans Serif

Colors
0054AA
0677BA
7BADD7
CADEEF
E8F1F8
EB3D1F
EC4F4E
F09395
F8D3D4
FCEDEE

Requirements
Must have
• Needs to look sharp and modern

```html
<!DOCTYPE html>
<html lang="en">
<head>
<meta charset="utf-8">
<title>Velmora Bath Co. – XL Clean Towels carton front</title>
<link href="https://fonts.googleapis.com/css2?family=Lora:wght@400;500&display=swap" rel="stylesheet">
<style>
  :root {
    --navy: #1a3667;
    --navy-deep: #142d5a;
    --navy-light: #1f4580;
    --board: #ebeced;
    --board-edge: #d6d8da;
    --slot: #e3e5e7;
    --slot-line: #c9ccd0;
    --page: #f4f4f4;
    --white: #ffffff;
  }
  * { box-sizing: border-box; margin: 0; padding: 0; }
  html, body {
    width: 770px;
    height: 1200px;
    overflow: hidden;
    background: var(--page);
  }
  body {
    font-family: "Lora", Georgia, serif;
    position: relative;
  }
  .carton-front {
    position: absolute;
    left: 45px;
    top: 306px;
    width: 680px;
    height: 588px;
    background: var(--board);
    border: 1px solid var(--board-edge);
    overflow: hidden;
  }
  .dispenser-flap {
    position: absolute;
    left: 76px;
    top: 0;
    width: 543px;
    height: 340px;
  }
  .dispenser-flap svg { display: block; }
  .brand-name {
    position: absolute;
    left: 0;
    right: 0;
    top: 150px;
    text-align: center;
    color: var(--white);
    font-size: 34px;
    font-weight: 400;
    letter-spacing: 1px;
  }
  .tear-slot {
    position: absolute;
    left: 44px;
    top: 296px;
    width: 602px;
    height: 70px;
  }
  .tear-slot svg { display: block; }
  .product-title {
    position: absolute;
    left: 0;
    right: 0;
    top: 385px;
    text-align: center;
    color: var(--navy);
    font-size: 26px;
    letter-spacing: 1.2px;
  }
  .product-features {
    position: absolute;
    left: 0;
    right: 0;
    top: 465px;
    text-align: center;
    color: var(--navy);
    font-size: 14px;
    line-height: 26px;
    letter-spacing: 1px;
  }
  .site-band {
    position: absolute;
    left: 0;
    right: 0;
    bottom: 0;
    height: 56px;
    background: var(--navy);
    color: var(--white);
    font-size: 16px;
    letter-spacing: 2.6px;
    text-align: center;
    line-height: 56px;
  }
  .count-badge {
    position: absolute;
    left: 555px;
    top: 491px;
    width: 78px;
    height: 78px;
  }
  .count-badge svg { position: absolute; inset: 0; }
  .count-badge .count-number {
    position: absolute;
    left: 0; right: 0;
    top: 14px;
    text-align: center;
    color: var(--white);
    font-size: 22px;
    line-height: 26px;
  }
  .count-badge .count-label {
    position: absolute;
    left: 0; right: 0;
    top: 40px;
    text-align: center;
    color: var(--white);
    font-size: 11px;
  }
</style>
</head>
<body>
  <main class="carton-front">
    <div class="tear-slot">
      <svg width="602" height="70" viewBox="0 0 602 70">
        <path d="M28 2 H574 A32 32 0 0 1 574 66 H28 A32 32 0 0 1 28 2 Z" fill="var(--slot)" stroke="var(--slot-line)" stroke-width="1.5" stroke-dasharray="24 6"/>
      </svg>
    </div>

    <div class="dispenser-flap">
      <svg width="543" height="340" viewBox="0 0 543 340">
        <defs>
          <linearGradient id="flapShade" x1="0" y1="0" x2="0" y2="1">
            <stop offset="0" stop-color="var(--navy-light)"/>
            <stop offset="1" stop-color="var(--navy-deep)"/>
          </linearGradient>
        </defs>
        <path d="M0 0 H543 V298 H330 L308 340 H238 L214 298 H0 Z" fill="url(#flapShade)"/>
      </svg>
      <div class="brand-name">VELMORA BATH CO.</div>
    </div>

    <h1 class="product-title">XL CLEAN TOWELS</h1>

    <p class="product-features">
      Ultra Soft &nbsp;|&nbsp; 100% USDA Bio–Based<br>
      100% Eucalyptus Viscose &nbsp;|&nbsp; Vegan
    </p>

    <footer class="site-band">www.velmorabathco.com</footer>

    <div class="count-badge">
      <svg width="78" height="78" viewBox="0 0 78 78">
        <rect x="17" y="17" width="44" height="44" rx="5" transform="rotate(45 39 39)" fill="var(--navy)" stroke="var(--white)" stroke-width="1.5"/>
      </svg>
      <div class="count-number">50</div>
      <div class="count-label">Count</div>
    </div>
  </main>
</body>
</html>
```